Unique Business Card Design

Unique Business Card design for our orthotic and prosthetic company. Our logo is on our website, color is light blue. Unique shape (artificial leg shaped, vertical, etc..) preferred. Logo, business name, individual name and basic demographics needed.

Industry/Entity Type

Business

Contact Information for Business Card

Logo, Industry, Phone # Logo, "Prosthetic & Orthotic Services" Place to add individual name and contact info

Colors
cee9f5

Requirements
Must have
• The icon must be there, placement of "Prosthetic & Orthotic Services" can be moved
Nice to have
• Like the mix of light blue, and a little darker blue. One design included the icons from my website which was a nice touch

```html
<!DOCTYPE html>
<html lang="en">
<head>
<meta charset="utf-8">
<title>Limbwell Inc. – Business Card</title>
<link rel="stylesheet" href="https://fonts.googleapis.com/css2?family=Open+Sans:wght@400;600;700&display=swap">
<style>
  :root {
    --brand-blue: #1560ae;
    --text-grey: #4f4f4f;
    --card-white: #ffffff;
    --backdrop: #4a4a4a;
  }
  * { margin: 0; padding: 0; box-sizing: border-box; }
  html, body { width: 1105px; height: 1200px; overflow: hidden; }
  body {
    background: var(--backdrop);
    font-family: "Open Sans", Arial, sans-serif;
    position: relative;
  }
  .card {
    position: absolute;
    left: 192px;
    width: 720px;
    height: 412px;
  }
  .card--front { top: 160px; background: var(--card-white); }
  .card--back { top: 628px; background: var(--brand-blue); }

  /* Front */
  .brand {
    position: absolute;
    top: 62px;
    left: 168px;
    display: flex;
    align-items: center;
    gap: 22px;
  }
  .brand__dot {
    width: 100px; height: 100px;
    border-radius: 50%;
    background: var(--brand-blue);
    flex: none;
  }
  .brand__text { display: flex; flex-direction: column; }
  .brand__name {
    font-weight: 700;
    font-size: 31px;
    line-height: 1;
    color: var(--brand-blue);
    padding-bottom: 6px;
    border-bottom: 2px solid var(--brand-blue);
  }
  .brand__tagline {
    margin-top: 6px;
    font-size: 15px;
    color: var(--brand-blue);
    text-align: center;
  }

  .person {
    position: absolute;
    top: 218px;
    left: 0; right: 0;
    text-align: center;
  }
  .person__name {
    font-weight: 600;
    font-size: 26px;
    line-height: 1.1;
    color: var(--brand-blue);
  }
  .person__title {
    margin-top: 4px;
    display: flex;
    justify-content: center;
    align-items: center;
    gap: 8px;
    font-weight: 600;
    font-size: 15px;
    color: var(--brand-blue);
  }
  .person__title::before,
  .person__title::after {
    content: "";
    width: 110px;
    height: 2px;
    background: var(--brand-blue);
  }

  .contact {
    position: absolute;
    top: 280px;
    left: 0; right: 0;
    font-size: 19px;
    color: var(--text-grey);
    text-align: center;
  }
  .contact__row {
    display: flex;
    justify-content: center;
    align-items: center;
    gap: 8px;
    height: 28px;
  }
  .contact__item { display: inline-flex; align-items: center; gap: 4px; }
  .contact__icon { width: 18px; height: 18px; fill: var(--brand-blue); }
  .contact__address { margin-top: 3px; }

  /* Back */
  .back-mark {
    position: absolute;
    left: 247px; top: 93px;
    width: 226px; height: 226px;
    border-radius: 50%;
    background: var(--card-white);
    display: flex;
    align-items: center;
    justify-content: center;
  }
  .back-mark__name {
    font-weight: 700;
    font-size: 27px;
    color: var(--brand-blue);
  }
  .back-web {
    position: absolute;
    top: 344px;
    left: 0; right: 0;
    text-align: center;
    font-size: 18px;
    letter-spacing: 4px;
    color: var(--card-white);
  }
</style>
</head>
<body>

<section class="card card--front">
  <div class="brand">
    <div class="brand__dot"></div>
    <div class="brand__text">
      <div class="brand__name">LIMBWELL INC.</div>
      <div class="brand__tagline">Prosthetic &amp; Orthotic Services</div>
    </div>
  </div>

  <div class="person">
    <div class="person__name">MIRA TALBROOK</div>
    <div class="person__title">CO LPO</div>
  </div>

  <div class="contact">
    <div class="contact__row">
      <span class="contact__item">
        <svg class="contact__icon" viewBox="0 0 24 24"><path d="M6.6 10.8a15.1 15.1 0 0 0 6.6 6.6l2.2-2.2c.3-.3.7-.4 1-.2 1.1.4 2.3.6 3.6.6.6 0 1 .4 1 1V20c0 .6-.4 1-1 1A17 17 0 0 1 3 4c0-.6.4-1 1-1h3.5c.6 0 1 .4 1 1 0 1.3.2 2.5.6 3.6.1.3 0 .7-.2 1z"/></svg>
        555.201.4400
      </span>
      <span class="contact__item">
        <svg class="contact__icon" viewBox="0 0 24 24"><path d="M7 1h10a2 2 0 0 1 2 2v18a2 2 0 0 1-2 2H7a2 2 0 0 1-2-2V3a2 2 0 0 1 2-2zm0 3v14h10V4zm5 15.5a1 1 0 1 0 0 2 1 1 0 0 0 0-2z"/></svg>
        555.201.4411
      </span>
      <span class="contact__item">
        <svg class="contact__icon" viewBox="0 0 24 24"><path d="M6 2h12v5H6zM3 8h18a2 2 0 0 1 2 2v7h-4v5H5v-5H1v-7a2 2 0 0 1 2-2zm4 8v4h10v-4z"/></svg>
        555-3806120
      </span>
    </div>
    <div class="contact__row">
      <span class="contact__item">
        <svg class="contact__icon" viewBox="0 0 24 24"><path d="M2 5h20v14H2zm2 2v.5l8 5 8-5V7l-8 5z"/></svg>
        mtalbrook@limbwellinc.com
      </span>
      <span class="contact__item">
        <svg class="contact__icon" viewBox="0 0 24 24"><path d="M12 2a10 10 0 1 0 0 20 10 10 0 0 0 0-20zm-1 17.9A8 8 0 0 1 4.2 10.6L9 15.4v1a2 2 0 0 0 2 2zm6.9-2.5A2 2 0 0 0 16 16h-1v-3a1 1 0 0 0-1-1H8v-2h2a1 1 0 0 0 1-1V7h2a2 2 0 0 0 2-2v-.4a8 8 0 0 1 2.9 12.8z"/></svg>
        www.limbwellinc.com
      </span>
    </div>
    <div class="contact__address">820 Harbor Ave., Fairview, NY 10020</div>
  </div>
</section>

<section class="card card--back">
  <div class="back-mark">
    <span class="back-mark__name">LIMBWELL INC.</span>
  </div>
  <div class="back-web">www.limbwellinc.com</div>
</section>

</body>
</html>
```